Business Card Design Project

Company Name - Solvane Care

Wellness consulting and training company. Run through a medical centre.

Main colour themes are orange and blue, as in the logo. Want to replicate same effect with business cards.

To give a sense of freedom and potential as per the company name.

Want the business card to be in line with stationary design, which I have launched as well.

Double sided with design and colour on one side and details on other side.

Reason: Need business card and stationary design to be teed up.

Target Market(s)

35 to 65 age group.
New age and trendy

Industry/Entity Type

Training

Requirements
Must have
• Colours orange and blue as per logo
Nice to have
• Design to be similar to stationary design, letterhead and envelopes

```html
<!DOCTYPE html>
<html lang="en">
<head>
<meta charset="utf-8">
<title>Solvane Care — Business Card</title>
<link href="https://fonts.googleapis.com/css2?family=Montserrat:wght@500;700;800&family=Pathway+Gothic+One&display=swap" rel="stylesheet">
<style>
  :root {
    --backdrop: #2b2b2d;
    --card: #f4f4f5;
    --blue: #1f5fa6;
    --blue-light: #3c7fc4;
    --orange: #e8731f;
    --ink: #222428;
  }
  * { box-sizing: border-box; margin: 0; padding: 0; }
  html, body { width: 1200px; height: 997px; overflow: hidden; }
  body { background: var(--backdrop); position: relative; font-family: "Montserrat", sans-serif; }

  .card {
    position: absolute;
    width: 600px; height: 343px;
    background: var(--card);
    border-radius: 18px;
    overflow: hidden;
    box-shadow: 0 18px 40px rgba(0,0,0,.45);
  }
  .card--front { left: 60px; top: 90px; }
  .card--back { left: 540px; top: 540px; }

  .band { position: absolute; left: 0; right: 0; background: var(--blue); }
  .band::after { content: ""; position: absolute; left: 0; right: 0; height: 5px; background: var(--orange); }
  .card--front .band { top: 0; height: 62px; }
  .card--front .band::after { bottom: -5px; }
  .card--back .band { bottom: 0; height: 30px; }
  .card--back .band::after { top: -5px; }

  .brand {
    position: absolute;
    display: flex; align-items: center; gap: 12px;
    font-family: "Pathway Gothic One", sans-serif;
    color: var(--blue);
    white-space: nowrap;
  }
  .brand__dot { border-radius: 50%; background: var(--orange); flex: none; }
  .card--front .brand { right: 70px; top: 160px; font-size: 68px; }
  .card--front .brand__dot { width: 22px; height: 22px; }
  .card--back .brand { left: 40px; top: 178px; font-size: 50px; }
  .card--back .brand__dot { width: 16px; height: 16px; }

  .divider {
    position: absolute; left: 300px; top: 28px; width: 4px; height: 255px;
    background: linear-gradient(to bottom, rgba(31,95,166,.15), var(--blue) 45%, rgba(31,95,166,.1));
  }

  .details { position: absolute; left: 330px; top: 30px; }
  .details__name { font-weight: 800; font-size: 21px; color: var(--blue); letter-spacing: .5px; }
  .details__role { font-weight: 700; font-size: 14px; color: var(--ink); margin-top: 1px; }
  .contacts { list-style: none; margin-top: 26px; }
  .contacts li {
    display: flex; align-items: center; gap: 10px;
    font-weight: 500; font-size: 14px; color: var(--ink);
    margin-bottom: 11px;
  }
  .contacts li:nth-child(2) { padding-left: 10px; }
  .contacts li:nth-child(3) { padding-left: 20px; }
  .contacts li:nth-child(4) { padding-left: 30px; }
  .icon {
    width: 28px; height: 28px; border-radius: 50%;
    background: var(--orange);
    display: flex; align-items: center; justify-content: center; flex: none;
  }
  .icon svg { width: 16px; height: 16px; }
</style>
</head>
<body>
  <section class="card card--front" aria-label="Card front">
    <div class="band"></div>
    <div class="brand"><span class="brand__dot"></span>Solvane Care</div>
  </section>

  <section class="card card--back" aria-label="Card back">
    <div class="brand"><span class="brand__dot"></span>Solvane Care</div>
    <div class="divider"></div>
    <div class="details">
      <p class="details__name">YOUR NAME</p>
      <p class="details__role">Centre Director</p>
      <ul class="contacts">
        <li><span class="icon"><svg viewBox="0 0 16 16"><path d="M2 5c0-2 1.5-2.5 6-2.5S14 3 14 5v1h-3V5H5v1H2z M4 7h8l1.5 6h-11z" fill="#fff"/></svg></span>+39 300 555 0142</li>
        <li><span class="icon"><svg viewBox="0 0 16 16"><path d="M4 2l2.5 3-1.5 1.5c.8 1.8 2.2 3.2 4 4L10.5 9l3 2.5-1.5 2.5C7 14 2 9 1.5 3.5z" fill="#fff"/></svg></span>(+123) 456 7890</li>
        <li><span class="icon"><svg viewBox="0 0 16 16"><rect x="2" y="4" width="12" height="8" fill="none" stroke="#fff" stroke-width="1.5"/><path d="M2 4l6 5 6-5" fill="none" stroke="#fff" stroke-width="1.5"/></svg></span>info@solvanecare.com</li>
        <li><span class="icon"><svg viewBox="0 0 16 16"><path d="M7 9l2-2 M6 6l-2 2a2 2 0 0 0 3 3l2-2 M10 10l2-2a2 2 0 0 0-3-3l-2 2" fill="none" stroke="#fff" stroke-width="1.6" stroke-linecap="round"/></svg></span>www.solvanecare.com</li>
      </ul>
    </div>
    <div class="band"></div>
  </section>
</body>
</html>
```